SaaS Early tech startup business card design

Unique design for experience ecommerce platform company. the business cards will be used by executive members. conformance with color code is required.

```html
<!DOCTYPE html>
<html lang="en">
<head>
<meta charset="utf-8">
<title>Nuvio Business Card</title>
<link href="https://fonts.googleapis.com/css2?family=Roboto:wght@400;700&display=swap" rel="stylesheet">
<style>
  :root {
    --bg: #d9d9db;
    --paper: #ffffff;
    --navy: #0b4a86;
    --teal: #12b39b;
    --ocean: #13789f;
    --ink: #4a4a4a;
  }
  * { margin: 0; padding: 0; box-sizing: border-box; }
  html, body { width: 1200px; height: 800px; overflow: hidden; }
  body {
    background: var(--bg);
    font-family: "Roboto", Arial, sans-serif;
    position: relative;
  }
  .card {
    position: absolute;
    top: 251px;
    width: 520px;
    height: 298px;
    border-radius: 2px;
    box-shadow: 0 6px 18px rgba(0,0,0,0.18);
    overflow: hidden;
  }
  .card--front { left: 60px; background: var(--paper); }
  .card--back { left: 620px; }

  .corner-squares { position: absolute; top: 0; right: 0; }

  .brand-name {
    position: absolute;
    left: 40px;
    top: 58px;
    font-size: 64px;
    font-weight: 700;
    color: var(--navy);
    letter-spacing: -1px;
    line-height: 1;
  }

  .holder {
    position: absolute;
    right: 44px;
    top: 118px;
    text-align: right;
  }
  .holder__name {
    font-size: 21px;
    font-weight: 700;
    color: var(--navy);
    letter-spacing: 0.3px;
  }
  .holder__title {
    font-size: 13px;
    color: var(--teal);
    margin-top: 2px;
  }

  .address {
    position: absolute;
    left: 42px;
    top: 150px;
    font-size: 12px;
    line-height: 15px;
    color: var(--ink);
  }
  .contacts {
    position: absolute;
    left: 42px;
    top: 190px;
    list-style: none;
    font-size: 12px;
    line-height: 15px;
    color: var(--ink);
  }
  .contacts li { display: flex; align-items: center; gap: 7px; }
  .contacts svg { width: 10px; height: 10px; flex: none; }

  .back-field {
    position: absolute;
    inset: 0;
    background: linear-gradient(135deg, var(--teal) 0%, var(--ocean) 50%, var(--navy) 100%);
  }
  .back-band {
    position: absolute;
    left: 60px;
    right: 60px;
    top: 92px;
    height: 114px;
    background: radial-gradient(ellipse at center, #1a86a8 0%, var(--navy) 100%);
  }
  .back-brand {
    position: absolute;
    left: 0;
    right: 0;
    top: 112px;
    text-align: center;
    font-size: 72px;
    font-weight: 700;
    color: #ffffff;
    line-height: 1;
    letter-spacing: -1px;
  }
</style>
</head>
<body>

  <section class="card card--front" aria-label="Business card front">
    <svg class="corner-squares" width="56" height="28" viewBox="0 0 56 28" aria-hidden="true">
      <rect x="0" y="0" width="28" height="14" fill="var(--teal)"/>
      <rect x="28" y="14" width="28" height="14" fill="var(--navy)"/>
    </svg>

    <div class="brand-name">Nuvio</div>

    <div class="holder">
      <div class="holder__name">DANIEL REYES</div>
      <div class="holder__title">President</div>
    </div>

    <address class="address" style="font-style:normal">
      1420 Harbor View Road<br>
      Juneau, Alaska 99801
    </address>

    <ul class="contacts">
      <li>
        <svg viewBox="0 0 10 10"><path d="M2 1 L4 1 L4.6 3 L3.4 3.8 C4 5.2 4.8 6 6.2 6.6 L7 5.4 L9 6 L9 8 C9 8.6 8.6 9 8 9 C4.2 9 1 5.8 1 2 C1 1.4 1.4 1 2 1Z" fill="var(--teal)"/></svg>
        555-214-7730
      </li>
      <li>
        <svg viewBox="0 0 10 10"><rect x="2.5" y="0.8" width="5" height="8.4" rx="1" fill="none" stroke="var(--teal)" stroke-width="1.2"/></svg>
        555-381-0462
      </li>
      <li>
        <svg viewBox="0 0 10 10"><rect x="1" y="4" width="8" height="5" fill="var(--teal)"/><rect x="2.5" y="1" width="5" height="3" fill="none" stroke="var(--teal)"/></svg>
        555-608-2195
      </li>
      <li>
        <svg viewBox="0 0 10 10"><rect x="0.8" y="2" width="8.4" height="6" fill="var(--teal)"/><path d="M1 2.3 L5 5.5 L9 2.3" fill="none" stroke="#fff" stroke-width="0.9"/></svg>
        name@nuvio.com
      </li>
      <li>
        <svg viewBox="0 0 10 10"><circle cx="5" cy="5" r="4.2" fill="var(--teal)"/><path d="M0.8 5 H9.2 M5 0.8 C3 3 3 7 5 9.2 M5 0.8 C7 3 7 7 5 9.2" fill="none" stroke="#fff" stroke-width="0.7"/></svg>
        www.nuvio.com
      </li>
    </ul>
  </section>

  <section class="card card--back" aria-label="Business card back">
    <div class="back-field" role="img" aria-label="Mosaic of teal and blue squares"></div>
    <div class="back-band"></div>
    <div class="back-brand">Nuvio</div>
  </section>

</body>
</html>
```